Website for International Non-Profit for Birth Parent Searching

LumaKin is a 501(c)(3) non-profit organization that helps Chinese adoptees search and reunite with birth families who were separated due the One Child Policy in China. We want to create a website that can link to an information database that allows website users to easily access information around search ads in an organized way; help connect families to professional searchers; provide resources for community support for adoptees and their families as they embark on a personal and emotional journey of finding birth family through support groups on social media and consultation/education on the searching process; and provide the opportunity for the adoptive community to give back through donations and volunteer opportunities. The final design should foster a sense of community and be easy navigable to access the multiple resources we provide to help families search for each other. We would like to see designs with red/black/white color schemes that are gentle, inviting, and family friendly to viewers. We would like to see some design layouts with Chinese themes, if possible.

```html
<!DOCTYPE html>
<html lang="en">
<head>
<meta charset="utf-8">
<title>LumaKin – International Non-Profit for Birth Parent Searching</title>
<link href="https://fonts.googleapis.com/css2?family=Cinzel:wght@700&family=Open+Sans:wght@400;600;700&display=swap" rel="stylesheet">
<style>
:root{
  --red:#c8111e;
  --coral:#e5685a;
  --ink:#333333;
  --text:#3f3f3f;
  --grey-bg:#f4f4f4;
  --blush:#f9e8e8;
  --white:#ffffff;
  --line:#e2d6d6;
}
*{margin:0;padding:0;box-sizing:border-box}
html,body{width:1200px;height:2802px;overflow:hidden}
body{position:relative;font-family:'Open Sans',sans-serif;color:var(--text);background:var(--white)}
.abs{position:absolute}
.serif{font-family:'Cinzel',serif;font-weight:700}
.center{left:0;width:1200px;text-align:center}

.site-header{top:0;left:0;width:1200px;height:120px;background:var(--white)}
.brand{left:145px;top:18px;display:flex;align-items:center;gap:14px}
.brand-mark{width:86px;height:86px;border-radius:50%;background:var(--red)}
.brand-name{font-family:'Cinzel',serif;font-weight:700;font-size:30px;color:var(--red)}
.main-nav a{font-size:13.5px;font-weight:600;color:var(--ink);text-decoration:none;position:absolute;white-space:nowrap}
.main-nav a.active{color:var(--red)}
.main-nav a.active::after{content:"";position:absolute;left:0;right:0;bottom:-8px;height:2px;background:var(--red)}

.hero{top:120px;left:0;width:1200px;height:574px;background:linear-gradient(120deg,#cf6b6d 0%,#d98486 45%,#c9686a 100%)}
.hero-title{top:232px;font-size:104px;color:var(--white);letter-spacing:2px;line-height:1}
.hero-sub{top:357px;font-size:18px;color:var(--white)}
.btn{display:flex;align-items:center;justify-content:center;border-radius:30px;font-weight:700;text-decoration:none;text-transform:uppercase}
.btn-solid{background:var(--red);color:var(--white)}
.btn-ghost{border:2px solid var(--white);color:var(--white)}
.btn-outline{border:2px solid var(--red);color:var(--red);background:transparent;font-size:12px}
.dot{top:623px;width:10px;height:10px;border-radius:50%;background:var(--white)}

.org-title{left:145px;top:772px;font-size:36px;color:var(--ink)}
.org-list{left:145px;top:830px;width:530px;list-style:none;font-size:17.4px;line-height:25px;color:var(--ink)}
.org-list li{position:relative;padding-left:23px;margin-bottom:13px}
.org-list li svg{position:absolute;left:0;top:6px}
.org-photo{left:708px;top:766px;width:350px;height:350px;border-radius:50%;border:6px solid var(--white);box-shadow:0 0 0 2px #e6e6e6;background:radial-gradient(circle at 60% 45%,#d9b7a8 0%,#c94a48 45%,#c8141f 75%,#2a5fa0 100%)}

.services{top:1183px;left:0;width:1200px;height:506px;background:var(--grey-bg)}
.sec-title{font-size:38px;color:var(--ink)}
.svc-icon{width:124px;height:124px;border-radius:50%;background:var(--red)}
.svc-name{width:300px;text-align:center;font-size:17px;font-weight:700;color:var(--ink)}
.svc-text{width:290px;text-align:center;font-size:15px;line-height:22px;color:var(--text)}

.video{top:1689px;left:0;width:1200px;height:368px;background:linear-gradient(135deg,#de5e52 0%,#e8776a 50%,#e26457 100%)}
.video-title{top:1745px;font-size:38px;color:var(--white)}
.video-text{top:1798px;left:160px;width:880px;text-align:center;font-size:15px;line-height:28px;color:var(--white)}

.contact{top:2057px;left:0;width:1200px;height:458px;background:var(--blush)}
.contact-text{top:2152px;left:190px;width:820px;text-align:center;font-size:12.5px;line-height:22px;color:var(--ink)}
.field{background:var(--white);border:1px solid var(--line);font-size:13.5px;color:#555;padding:10px 16px}

.site-footer{top:2515px;left:0;width:1200px;height:287px;background:var(--red);color:var(--white)}
.foot-head{font-size:15px;color:var(--white);letter-spacing:.5px}
.foot-link{font-size:11.5px;color:var(--white)}
.foot-rule{top:2752px;left:145px;width:911px;height:1px;background:rgba(255,255,255,.45)}
.copyright{top:2768px;font-size:11px;color:var(--white)}
.ico{display:inline-block;vertical-align:middle;margin-right:5px}
</style>
</head>
<body>

<header class="abs site-header">
  <div class="abs brand">
    <span class="brand-mark"></span>
    <span class="brand-name">LUMAKIN</span>
  </div>
  <nav class="abs main-nav" style="left:0;top:54px">
    <a class="active" href="#" style="left:471px">HOME</a>
    <a href="#" style="left:551px">ABOUT US</a>
    <a href="#" style="left:658px">OUR SERVICES</a>
    <a href="#" style="left:790px">PARTNERS</a>
    <a href="#" style="left:897px">BLOG</a>
    <a href="#" style="left:973px">CONTACT US</a>
  </nav>
</header>

<section class="abs hero" role="img" aria-label="Soft red-tinted photo of a newborn held in a parent's hands"></section>
<h1 class="abs center serif hero-title">LUMAKIN</h1>
<p class="abs center hero-sub">We are an International Non-Profit for Birth Parent Searching</p>
<a class="abs btn btn-solid" href="#" style="left:438px;top:413px;width:156px;height:48px;font-size:16px">Donate Now</a>
<a class="abs btn btn-ghost" href="#" style="left:606px;top:413px;width:156px;height:48px;font-size:16px">Search Add</a>
<span class="abs dot" style="left:580px;background:transparent;border:1px solid #fff"></span>
<span class="abs dot" style="left:596px"></span>
<span class="abs dot" style="left:612px"></span>

<h2 class="abs serif org-title">Our Organized Way</h2>
<ul class="abs org-list">
  <li><svg width="13" height="13" viewBox="0 0 13 13"><circle cx="6.5" cy="6.5" r="6.5" fill="#c8111e"/><path d="M3 6.5h6M6.5 3.8l2.7 2.7-2.7 2.7" stroke="#fff" stroke-width="1.6" fill="none"/></svg>Help connect families to professional searchers</li>
  <li><svg width="13" height="13" viewBox="0 0 13 13"><circle cx="6.5" cy="6.5" r="6.5" fill="#c8111e"/><path d="M3 6.5h6M6.5 3.8l2.7 2.7-2.7 2.7" stroke="#fff" stroke-width="1.6" fill="none"/></svg>Provide resources for community support for adoptees and their families as they embark on a personal and emotional journey of finding birth family through support groups on social media and consultation/education on the searching process</li>
  <li><svg width="13" height="13" viewBox="0 0 13 13"><circle cx="6.5" cy="6.5" r="6.5" fill="#c8111e"/><path d="M3 6.5h6M6.5 3.8l2.7 2.7-2.7 2.7" stroke="#fff" stroke-width="1.6" fill="none"/></svg>Provide the opportunity for the adoptive community to give back through donations and volunteer opportunities</li>
</ul>
<a class="abs btn btn-solid" href="#" style="left:145px;top:1073px;width:148px;height:42px;font-size:16px">Learn More</a>
<div class="abs org-photo" role="img" aria-label="Circular photo of a mother holding hands with her newborn, tinted red"></div>

<section class="abs services"></section>
<h2 class="abs center serif sec-title" style="top:1225px">OUR SERVICES</h2>
<svg class="abs" style="left:84px;top:1428px" width="26" height="44" viewBox="0 0 26 44"><path d="M22 3 4 22l18 19" stroke="#b5b5b5" stroke-width="5" fill="none"/></svg>
<svg class="abs" style="left:1083px;top:1428px" width="26" height="44" viewBox="0 0 26 44"><path d="M4 3l18 19L4 41" stroke="#b5b5b5" stroke-width="5" fill="none"/></svg>

<span class="abs svc-icon" style="left:228px;top:1308px"></span>
<p class="abs svc-name" style="left:132px;top:1448px">FINIBUS BONORUM</p>
<p class="abs svc-text" style="left:137px;top:1479px">Exercitation ullamco laboris nisi ut aliquip ex ea commodo consequat velit esse cillum dolore eu fugiat.</p>
<a class="abs btn btn-outline" href="#" style="left:223px;top:1569px;width:120px;height:39px">Learn More</a>

<span class="abs svc-icon" style="left:545px;top:1308px"></span>
<p class="abs svc-name" style="left:450px;top:1448px">NECESSITATIBUS SAEPE</p>
<p class="abs svc-text" style="left:455px;top:1479px">Exercitation ullamco laboris nisi ut aliquip ex ea commodo consequat velit esse cillum dolore eu fugiat.</p>
<a class="abs btn btn-outline" href="#" style="left:541px;top:1569px;width:120px;height:39px">Learn More</a>

<span class="abs svc-icon" style="left:862px;top:1308px"></span>
<p class="abs svc-name" style="left:767px;top:1448px">OFFICIA DESERUNT</p>
<p class="abs svc-text" style="left:772px;top:1479px">Exercitation ullamco laboris nisi ut aliquip ex ea commodo consequat velit esse cillum dolore eu fugiat.</p>
<a class="abs btn btn-outline" href="#" style="left:858px;top:1569px;width:120px;height:39px">Learn More</a>

<section class="abs video" role="img" aria-label="Coral-tinted photo of a baby's tiny hands"></section>
<h2 class="abs center serif video-title">LUMAKIN VIDEO</h2>
<p class="abs video-text">At vero eos et accusamus et iusto odio dignissimos ducimus qui blanditiis praesentium voluptatum deleniti atque corrupti quos dolores et quas molestias excepturi sint occaecati cupiditate non provident</p>
<svg class="abs" style="left:562px;top:1883px" width="76" height="76" viewBox="0 0 76 76"><circle cx="38" cy="38" r="35.5" stroke="#fff" stroke-width="3" fill="none"/><path d="M29 23v30l24-15z" stroke="#fff" stroke-width="3" fill="none" stroke-linejoin="round"/></svg>

<section class="abs contact"></section>
<h2 class="abs center serif sec-title" style="top:2102px">CONTACT US</h2>
<p class="abs contact-text">Temporibus autem quibusdam et aut officiis debitis aut rerum necessitatibus saepe eveniet ut et voluptates repudiandae sint et molestiae non recusandae. Itaque earum rerum hic tenetur a sapiente delectus, ut aut reiciendis voluptatibus maiores</p>
<div class="abs field" style="left:144px;top:2219px;width:295px;height:40px">Your Name</div>
<div class="abs field" style="left:452px;top:2219px;width:295px;height:40px">Your Email</div>
<div class="abs field" style="left:761px;top:2219px;width:295px;height:40px">Your Phone</div>
<div class="abs field" style="left:144px;top:2274px;width:912px;height:84px">Your Message</div>
<a class="abs btn btn-solid" href="#" style="left:520px;top:2401px;width:161px;height:48px;font-size:16px">Submit Now</a>

<footer class="abs site-footer"></footer>
<h3 class="abs serif foot-head" style="left:145px;top:2558px">QUICK LINKS</h3>
<h3 class="abs serif foot-head" style="left:592px;top:2558px">CONTACT US</h3>
<h3 class="abs serif foot-head" style="left:906px;top:2558px">CONNECT WITH US</h3>

<a class="abs foot-link" style="left:145px;top:2604px">Home</a>
<a class="abs foot-link" style="left:145px;top:2632px">About Us</a>
<a class="abs foot-link" style="left:145px;top:2660px">Services</a>
<a class="abs foot-link" style="left:145px;top:2688px">Contact</a>
<a class="abs foot-link" style="left:353px;top:2604px">Latest Blog</a>
<a class="abs foot-link" style="left:353px;top:2632px">Terms of Use</a>
<a class="abs foot-link" style="left:353px;top:2660px">Privacy Policy</a>

<p class="abs foot-link" style="left:592px;top:2604px;line-height:15px"><svg class="ico" width="9" height="12" viewBox="0 0 9 12"><path d="M4.5 0A4.5 4.5 0 0 0 0 4.5C0 8 4.5 12 4.5 12S9 8 9 4.5A4.5 4.5 0 0 0 4.5 0z" fill="#fff"/><circle cx="4.5" cy="4.5" r="1.7" fill="#c8111e"/></svg>LumaKin, Street Address<br><span style="padding-left:17px">PO Box 48 Dorrow, MA 01987</span></p>
<p class="abs foot-link" style="left:592px;top:2654px"><svg class="ico" width="12" height="12" viewBox="0 0 12 12"><path d="M2.5 0.5l2 2.5-1.2 1.4c.8 1.7 2 2.9 3.6 3.6L8.3 6.8l2.7 2-1 2.4C5 11 1 7 .6 1.6z" fill="#fff"/></svg>017-482-5530</p>
<p class="abs foot-link" style="left:592px;top:2688px"><svg class="ico" width="12" height="9" viewBox="0 0 12 9"><rect width="12" height="9" rx="1" fill="#fff"/><path d="M.5 .8 6 5l5.5-4.2" stroke="#c8111e" fill="none"/></svg>hello@lumakin.org</p>

<p class="abs foot-link" style="left:906px;top:2604px"><svg class="ico" width="8" height="8"><circle cx="4" cy="4" r="4" fill="#fff"/></svg>Community Page</p>
<p class="abs foot-link" style="left:906px;top:2632px"><svg class="ico" width="8" height="8"><circle cx="4" cy="4" r="4" fill="#fff"/></svg>Network Page</p>
<p class="abs foot-link" style="left:906px;top:2660px"><svg class="ico" width="8" height="8"><circle cx="4" cy="4" r="4" fill="#fff"/></svg>Photo Feed</p>
<p class="abs foot-link" style="left:906px;top:2688px"><svg class="ico" width="8" height="8"><circle cx="4" cy="4" r="4" fill="#fff"/></svg>Video Channel</p>

<div class="abs foot-rule"></div>
<p class="abs center copyright">Copyrights © 2021 LumaKin. All rights reserved.</p>

</body>
</html>
```